Executive recruiting firm in need of business card design

Executive recruiting firm looking for a sleek, classy and modern business card design; card itself will be square shape, rounded edges and soft touch paper, our colors are dark blues in the navy color scale, silvers and grays. Reference our website for a better idea of our company's feel and goals at Tarvex-Up.com - our company message is "Great Teams Start With the Right Hire" this should be on the card

```html
<!DOCTYPE html>
<html lang="en">
<head>
<meta charset="utf-8">
<title>Tarvex Up – Business Card</title>
<link rel="stylesheet" href="https://fonts.googleapis.com/css2?family=Roboto:wght@300;400;500&display=swap">
<style>
  :root {
    --navy: #15174a;
    --paper: #f1f1f1;
    --white: #ffffff;
    --stage: #e4e4e6;
  }
  * { margin: 0; padding: 0; box-sizing: border-box; }
  html, body { width: 1200px; height: 960px; overflow: hidden; }
  body {
    background: var(--stage);
    font-family: "Roboto", Arial, sans-serif;
    position: relative;
  }
  .card {
    position: absolute;
    width: 600px;
    height: 343px;
    overflow: hidden;
  }
  .card--front { left: 314px; top: 113px; background: var(--navy); color: var(--white); }
  .card--back { left: 311px; top: 472px; background: var(--paper); color: var(--navy); }

  .brand { position: absolute; display: flex; align-items: center; }
  .brand__square { width: 18px; height: 18px; margin-right: 14px; }
  .brand__name {
    font-weight: 400;
    font-size: 38px;
    line-height: 1;
  }
  .card--front .brand { left: 38px; top: 82px; }
  .card--front .brand__square { background: var(--white); }
  .card--back .brand { left: 0; right: 0; top: 134px; justify-content: center; }
  .card--back .brand__square { background: var(--navy); }

  .contact {
    position: absolute;
    right: 24px;
    top: 116px;
    text-align: right;
  }
  .contact__name { font-weight: 500; font-size: 20px; line-height: 24px; }
  .contact__role { font-weight: 400; font-size: 15px; line-height: 22px; }
  .contact__address { font-size: 14px; line-height: 18px; margin-top: 10px; font-weight: 400; }
  .contact__list { list-style: none; margin-top: 10px; }
  .contact__item {
    display: flex; justify-content: flex-end; align-items: center;
    font-size: 14px; line-height: 19.5px; font-weight: 400;
  }
  .contact__item svg { width: 13px; height: 13px; margin-left: 8px; fill: var(--white); }

  .motto {
    position: absolute;
    left: 0; right: 0; top: 280px; height: 35px;
    background: var(--navy);
    color: var(--white);
    font-size: 15px;
    font-weight: 400;
    display: flex; align-items: center; justify-content: center;
  }
</style>
</head>
<body>
  <section class="card card--front">
    <div class="brand">
      <span class="brand__square"></span>
      <span class="brand__name">Tarvex Up</span>
    </div>

    <div class="contact">
      <div class="contact__name">DANA MORROW</div>
      <div class="contact__role">CEO/FOUNDER</div>
      <div class="contact__address">240 Marlow Ave.<br>Linden, CA</div>
      <ul class="contact__list">
        <li class="contact__item">555 210 4471
          <svg viewBox="0 0 16 16" aria-hidden="true"><path d="M3.6 1.2l2.6 2.6-1.5 2a9 9 0 0 0 5.5 5.5l2-1.5 2.6 2.6-1.7 2.1C6.8 14.3 1.7 9.2 1.5 2.9z"/></svg></li>
        <li class="contact__item">555 382 9016
          <svg viewBox="0 0 16 16" aria-hidden="true"><path d="M4.5 0h7a1 1 0 0 1 1 1v14a1 1 0 0 1-1 1h-7a1 1 0 0 1-1-1V1a1 1 0 0 1 1-1zm.8 1.8v10.6h5.4V1.8zM8 13.2a.9.9 0 1 0 0 1.8.9.9 0 0 0 0-1.8z"/></svg></li>
        <li class="contact__item">555 647 2803
          <svg viewBox="0 0 16 16" aria-hidden="true"><path d="M4 1h8v4H4zM1.5 6h13a1 1 0 0 1 1 1v5h-3v3h-9v-3h-3V7a1 1 0 0 1 1-1zm3 5v2.5h7V11z"/></svg></li>
        <li class="contact__item">dana@tarvex-up.com
          <svg viewBox="0 0 16 16" aria-hidden="true"><path d="M1 3.5h14v.8L8 9 1 4.3zM1 5.8l7 4.7 7-4.7V12.5H1z"/></svg></li>
        <li class="contact__item">www.tarvex-up.com
          <svg viewBox="0 0 16 16" aria-hidden="true"><path d="M8 1a7 7 0 1 0 0 14A7 7 0 0 0 8 1zm0 1.5c.8.9 1.4 2.4 1.6 4.5H6.4C6.6 4.9 7.2 3.4 8 2.5zM6.4 9h3.2c-.2 2.1-.8 3.6-1.6 4.5-.8-.9-1.4-2.4-1.6-4.5zM2.6 7a5.5 5.5 0 0 1 2.6-3.9C4.8 4.2 4.5 5.5 4.4 7zm0 2h1.8c.1 1.5.4 2.8.8 3.9A5.5 5.5 0 0 1 2.6 9zm8.2-5.9A5.5 5.5 0 0 1 13.4 7h-1.8c-.1-1.5-.4-2.8-.8-3.9zM11.6 9h1.8a5.5 5.5 0 0 1-2.6 3.9c.4-1.1.7-2.4.8-3.9z"/></svg></li>
      </ul>
    </div>
  </section>

  <section class="card card--back">
    <div class="brand">
      <span class="brand__square"></span>
      <span class="brand__name">Tarvex Up</span>
    </div>
    <div class="motto">Great Teams Start With the Right Hire</div>
  </section>
</body>
</html>
```